Need Business Card for our Real Estate Business with Sales Executive's Picture

PANTONE 484 C ( RED)

PANTONE 2766 C ( BLUE

Industry/Entity Type

Real Estate

Contact Information for Business Card

Name, Mobile, email, & picture of Person
Agency Phone, address, Web address

Requirements
Must have
• Our Logo Colours, Agent Picture,

```html
<!DOCTYPE html>
<html lang="en">
<head>
<meta charset="utf-8">
<title>Mirage Realty – Business Card</title>
<link href="https://fonts.googleapis.com/css2?family=Open+Sans:wght@400;600;700&display=swap" rel="stylesheet">
<style>
  :root {
    --navy: #1b2a5e;
    --navy-deep: #152350;
    --red: #a8282c;
    --white: #ffffff;
    --soft-white: #dfe4f2;
    --page: #e4e4e4;
  }
  * { box-sizing: border-box; margin: 0; padding: 0; }
  html, body { width: 1200px; height: 852px; overflow: hidden; }
  body {
    background: var(--page);
    font-family: "Open Sans", Arial, sans-serif;
    position: relative;
  }
  .card {
    position: absolute;
    top: 276px;
    width: 525px;
    height: 300px;
    border-radius: 22px;
    background: var(--navy);
    overflow: hidden;
    color: var(--white);
  }
  .card--front { left: 50px; }
  .card--back { left: 625px; }

  /* Front */
  .brand {
    position: absolute;
    left: 0; right: 0; top: 96px;
    text-align: center;
  }
  .brand__mark {
    display: inline-block;
    width: 12px; height: 12px;
    background: var(--red);
    margin-right: 12px;
    vertical-align: middle;
  }
  .brand__name {
    font-size: 48px;
    font-weight: 400;
    letter-spacing: 8px;
    vertical-align: middle;
  }
  .brand__rule {
    width: 250px; height: 1px;
    background: var(--soft-white);
    margin: 10px auto 0;
  }
  .front-web {
    position: absolute;
    left: 0; right: 0; top: 222px;
    display: flex; align-items: center; justify-content: center; gap: 14px;
    font-size: 14px;
    letter-spacing: .3px;
  }
  .front-web__rule {
    width: 50px; height: 3px;
    background: var(--red);
  }

  /* Back */
  .name-band {
    position: absolute;
    left: 0; top: 88px;
    width: 300px; height: 56px;
    background: var(--red);
    padding: 8px 0 0 26px;
  }
  .name-band__name { font-size: 18px; font-weight: 700; line-height: 1.25; }
  .name-band__title { font-size: 12px; line-height: 1.3; }
  .agent-photo {
    position: absolute;
    right: 0; top: 34px;
    width: 215px; height: 252px;
    background: linear-gradient(160deg, #2c4aa0 0%, #2a3f86 55%, #1d2f6e 100%);
  }
  .contact {
    position: absolute;
    left: 26px; top: 174px;
    font-size: 12.5px;
    line-height: 1.5;
    list-style: none;
  }
  .contact__address { margin-bottom: 4px; }
  .contact__row { display: flex; align-items: center; gap: 10px; }
  .contact__row svg { width: 12px; height: 12px; flex: none; }
  .bottom-strip {
    position: absolute;
    left: 0; right: 0; bottom: 0;
    height: 12px;
    background: var(--red);
  }
</style>
</head>
<body>
  <section class="card card--front">
    <div class="brand">
      <span class="brand__mark"></span><span class="brand__name">MIRAGE</span>
      <div class="brand__rule"></div>
    </div>
    <div class="front-web">
      <span class="front-web__rule"></span>
      <span>www.miragerealty.com</span>
      <span class="front-web__rule"></span>
    </div>
  </section>

  <section class="card card--back">
    <div class="name-band">
      <p class="name-band__name">Diana Whitlow</p>
      <p class="name-band__title">Managing Director</p>
    </div>
    <div class="agent-photo" role="img" aria-label="Portrait photo of the agent in a blue suit"></div>
    <ul class="contact">
      <li class="contact__address">418 Alder Way #2210,<br>Brookfield, CO 80310</li>
      <li class="contact__row">
        <svg viewBox="0 0 12 12"><rect x="3" y="0.5" width="6" height="11" rx="1" fill="none" stroke="#fff" stroke-width="1.2"/><circle cx="6" cy="9.5" r=".8" fill="#fff"/></svg>
        <span>555.214.7730</span>
      </li>
      <li class="contact__row">
        <svg viewBox="0 0 12 12"><path d="M2.5 1 L4.5 1 L5.5 3.5 L4.2 4.6 Q5.2 6.8 7.4 7.8 L8.5 6.5 L11 7.5 L11 9.5 Q10.5 11 9 11 Q1 10 1 3 Q1 1.5 2.5 1Z" fill="#fff"/></svg>
        <span>555-316-4482</span>
      </li>
      <li class="contact__row">
        <svg viewBox="0 0 12 12"><rect x="0.5" y="2.5" width="11" height="7" fill="#fff"/><path d="M0.5 2.5 L6 6.5 L11.5 2.5" fill="none" stroke="#1b2a5e" stroke-width="1"/></svg>
        <span>dwhitlow@miragerealty.com</span>
      </li>
      <li class="contact__row">
        <svg viewBox="0 0 12 12"><circle cx="6" cy="6" r="5.2" fill="none" stroke="#fff" stroke-width="1.1"/><ellipse cx="6" cy="6" rx="2.2" ry="5.2" fill="none" stroke="#fff" stroke-width="1"/><line x1=".8" y1="6" x2="11.2" y2="6" stroke="#fff" stroke-width="1"/></svg>
        <span>www.miragerealty.com</span>
      </li>
    </ul>
    <div class="bottom-strip"></div>
  </section>
</body>
</html>
```